Business Card Design & Gift cards, Gift Cert, Donation Card

Retail Gift Store-in addition to Business Cards we'd like sequenced 2 sided Gift cards, Gift Certificate Cards, and Donation Cards.please see examples and email for clarificationlogos attached with examples-
Gift Card, Gift Certificate and Donation Card will all be same style just differant upper right title, with back side info as example.
business card, as example is single sided.
looking for additional ideas for layout

Industry/Entity Type

Business

Contact Information for Business Card

211 Newman St.East Tawas, MI 48730989.362.8730Office@BrewKrew.com

Requirements
Must have
• Blue as per example
• Logos provided
• like gradiant background

```html
<!DOCTYPE html>
<html lang="en">
<head>
<meta charset="utf-8">
<title>Tillow Marsh – Business Card</title>
<link href="https://fonts.googleapis.com/css2?family=Kalam:wght@400;700&display=swap" rel="stylesheet">
<style>
  :root {
    --backdrop: #a4a4a4;
    --sky-top: #78b6f7;
    --sky-bottom: #bfe3f4;
    --frame-blue: #0b33d8;
    --brand-blue: #1a2fcf;
    --ink: #111a2c;
    --accent-red: #e4111c;
    --sun: #f6e300;
    --sun-faint: #c9dfb4;
  }
  * { margin: 0; padding: 0; box-sizing: border-box; }
  html, body { width: 992px; height: 1200px; overflow: hidden; }
  body {
    background: var(--backdrop);
    position: relative;
    font-family: "Kalam", cursive;
  }
  .card {
    position: absolute;
    left: 100px;
    width: 806px;
    height: 461px;
    background: linear-gradient(to bottom, var(--sky-top), var(--sky-bottom));
    overflow: hidden;
  }
  .card--front { top: 104px; border: 15px solid var(--frame-blue); }
  .card--back { top: 624px; }

  .brand-mark { position: absolute; }
  .card--front .brand-mark { left: 48px; top: 130px; width: 150px; height: 150px; }
  .card--back .brand-mark { left: 110px; top: 260px; width: 200px; height: 200px; }

  .brand-name {
    position: absolute;
    color: var(--brand-blue);
    font-weight: 400;
    line-height: 1;
    white-space: nowrap;
  }
  .card--front .brand-name { right: 40px; top: 52px; font-size: 92px; }
  .card--back .brand-name { left: 0; right: 0; top: 130px; text-align: center; font-size: 140px; }

  .contact {
    position: absolute;
    right: 30px;
    top: 196px;
    text-align: right;
    color: var(--ink);
    font-size: 24px;
    line-height: 31px;
    letter-spacing: 1px;
  }
  .contact .phone { margin-bottom: 6px; }

  .offerings {
    position: absolute;
    font-size: 20px;
    line-height: 30px;
    letter-spacing: 0.8px;
    white-space: nowrap;
  }
  .card--front .offerings { right: 30px; top: 336px; text-align: right; color: var(--ink); }
  .card--back .offerings {
    left: 0; right: 0; top: 302px; text-align: center;
    color: var(--accent-red); font-size: 24px; line-height: 35px; letter-spacing: 1px;
  }
</style>
</head>
<body>
  <section class="card card--front" aria-label="Business card front">
    <svg class="brand-mark" viewBox="0 0 100 100" aria-hidden="true">
      <circle cx="50" cy="50" r="48" fill="var(--sun)"/>
    </svg>
    <h1 class="brand-name">Tillow Marsh</h1>
    <address class="contact" style="font-style: normal;">
      <p class="phone">989·517·4296</p>
      <p>482 Larkfield Ave.</p>
      <p>Harlow Bay, MI 48761</p>
    </address>
    <p class="offerings">Gourmet Food, Fine Wines, Gift Baskets<br>Kitchen &amp; Bath Accessories, Candles, Cards, Soaps</p>
  </section>

  <section class="card card--back" aria-label="Business card back">
    <svg class="brand-mark" viewBox="0 0 100 100" aria-hidden="true">
      <circle cx="50" cy="50" r="48" fill="var(--sun-faint)" opacity="0.8"/>
    </svg>
    <h2 class="brand-name">Tillow Marsh</h2>
    <p class="offerings">Gourmet Food, Fine Wines, Gift Baskets<br>Kitchen &amp; Bath Accessories, Candles, Cards, Soaps</p>
  </section>
</body>
</html>
```